Business Cards for IT Consulting Company (Managed Service Provider)

I am looking to have some business cards printed and would like some designs. We are an IT Consulting company based in Vancouver BC. I would like a nice clean and modern look to the cards. I have uploaded all the versions of my logo so parts can be used as needed. Here is a snippit from our website homepage:

Quillbrook Networks Ltd. is an IT Solutions Partner located in Vancouver BC, Canada. We offer IT solutions and support to customers in the greater Vancouver Area. With expertise in Microsoft platforms, as well as Linux and Mac OSX and over 12 years experience in the IT industry, Quillbrook Networks is dedicated to offering our clients top quality service and products. We take pride in the solutions we offer our customers. The greatest compliment a client can give us is to recommend our services.

Quillbrook Networks Ltd. offers a wide range of IT services from onsite service to remote support and managed service solutions. This allows clients to choose the support path that best suits their company’s needs. Supporting many different sized companies from small to enterprise level over the past 12 years Quillbrook Networks has the experience and expertise needed to ensure things run smoothly. Allowing our clients to focus on doing business.

Revolutionizing the way IT services are delivered.

Quillbrook Networks is dedicated to providing our clients with IT solutions that work and grow with them for years to come. This philosophy helps save money in the long run instead of replacing equipment constantly. Far too often IT solutions are not well thought out and while possibly solving the problem at hand, require replacement due to growth or quality within a very short time frame. Quillbrook Networks takes pride in providing solutions that will last and be able to accommodate growth without the need for replacement.

Industry/Entity Type

Information Technology

Contact Information for Business Card

Quillbrook Networks Ltd.
(Employee Name)
Eml: (Employees Email Address)
Web: quillbrook.me
Ph: 604-555-0148

Font styles to use
Serif
Sans Serif

Requirements
Must have
• The Company logo and company colors.
Nice to have
• - Our tag line: "Revolutionizing IT Services" or "Revolutionizing the way IT services are delivered."
• - Also I really like the idea of nature and technology together blending which is sort of where my logo came from so integrating that somehow onto the business cards would be great.

```html
<!DOCTYPE html>
<html lang="en">
<head>
<meta charset="utf-8">
<title>Quillbrook Networks Ltd. – Business Cards</title>
<link rel="stylesheet" href="https://fonts.googleapis.com/css2?family=Montserrat:wght@500;600;700&display=swap">
<style>
  :root {
    --backdrop: #2b2b2c;
    --card-black: #030303;
    --brand-blue: #10a9ec;
    --band-grey: #636466;
    --text-white: #ffffff;
    --text-grey: #9a9b9d;
  }
  * { box-sizing: border-box; margin: 0; padding: 0; }
  html, body { width: 1200px; height: 900px; overflow: hidden; }
  body {
    background: var(--backdrop);
    font-family: "Montserrat", Arial, sans-serif;
    position: relative;
  }
  .card {
    position: absolute;
    width: 640px;
    height: 366px;
    background: var(--card-black);
    overflow: hidden;
    box-shadow: 0 14px 30px rgba(0,0,0,.45);
  }
  .card--front { left: 60px; top: 70px; }
  .card--back { left: 500px; top: 464px; }

  .brand-mark {
    display: flex;
    align-items: center;
    gap: 12px;
    color: var(--brand-blue);
    font-weight: 700;
    white-space: nowrap;
  }
  .brand-mark__dot {
    width: 14px; height: 14px;
    background: var(--brand-blue);
    flex: none;
  }

  .card--front .brand-block {
    position: absolute;
    left: 120px; top: 140px;
  }
  .card--front .brand-mark { font-size: 30px; }
  .tagline {
    margin-top: 14px;
    margin-left: 26px;
    color: var(--text-white);
    font-size: 17px;
    font-weight: 600;
    letter-spacing: 1.5px;
  }

  .side-band {
    position: absolute;
    left: 0; top: 0;
    width: 200px; height: 100%;
    background: var(--band-grey);
  }

  .details {
    position: absolute;
    right: 40px; top: 46px;
    text-align: right;
  }
  .card--back .brand-mark { font-size: 22px; justify-content: flex-end; }
  .person { margin-top: 34px; }
  .person__name {
    color: var(--brand-blue);
    font-size: 22px;
    font-weight: 700;
    letter-spacing: 2px;
  }
  .person__role {
    color: var(--text-white);
    font-size: 13px;
    font-weight: 600;
    letter-spacing: 2px;
    margin-top: 4px;
  }
  .contact-list { list-style: none; margin-top: 30px; }
  .contact-list li {
    display: flex;
    justify-content: flex-end;
    align-items: center;
    gap: 10px;
    color: var(--text-white);
    font-size: 14px;
    font-weight: 600;
    letter-spacing: 1px;
    margin-bottom: 10px;
  }
  .contact-list svg { width: 14px; height: 14px; flex: none; }
  .corner-tab {
    position: absolute;
    right: 0; top: 60px;
    width: 22px; height: 22px;
    background: var(--text-white);
  }
</style>
</head>
<body>

  <section class="card card--front" aria-label="Card front">
    <div class="brand-block">
      <div class="brand-mark"><span class="brand-mark__dot"></span>Quillbrook Networks Ltd.</div>
      <p class="tagline">Revolutionizing IT Services</p>
    </div>
  </section>

  <section class="card card--back" aria-label="Card back">
    <div class="side-band"></div>
    <div class="corner-tab"></div>
    <div class="details">
      <div class="brand-mark">Quillbrook Networks Ltd.</div>
      <div class="person">
        <p class="person__name">MARLA PENROSE</p>
        <p class="person__role">DIRECTOR</p>
      </div>
      <ul class="contact-list">
        <li>604-555-0148
          <svg viewBox="0 0 16 16" aria-hidden="true"><path d="M4 1.5l2.2 3-1.3 1.6a9 9 0 0 0 5 5l1.6-1.3 3 2.2-1.3 2.5C8 14.5 1.5 8 1.5 2.8z" fill="var(--brand-blue)"/></svg>
        </li>
        <li>info@marlapenrose.com
          <svg viewBox="0 0 16 16" aria-hidden="true"><rect x="1.5" y="3.5" width="13" height="9" fill="none" stroke="var(--brand-blue)" stroke-width="1.6"/><path d="M1.5 3.5L8 9l6.5-5.5" fill="none" stroke="var(--brand-blue)" stroke-width="1.6"/></svg>
        </li>
        <li>www.quillbrook.me
          <svg viewBox="0 0 16 16" aria-hidden="true"><circle cx="8" cy="8" r="6.5" fill="none" stroke="var(--brand-blue)" stroke-width="1.5"/><ellipse cx="8" cy="8" rx="2.8" ry="6.5" fill="none" stroke="var(--brand-blue)" stroke-width="1.3"/><path d="M1.5 8h13" stroke="var(--brand-blue)" stroke-width="1.3"/></svg>
        </li>
      </ul>
    </div>
  </section>

</body>
</html>
```